Business cards in digital learning for freelancer

Hello, I need a business cards in french. I work in the Digital learning industries as freeelancer; I'm an expert in digital learning. I work in France. My customer are in the health industry, pharmaceutical industry, and training organization. I've got a logo. I offer three services: consulting, Design, and Training. In the consulting, I offers coaching to choose your digital learning tools and the digital learning strategy. For the Design, I product differents level of elearning like rapid-learning, elearning, micro-learning, video-learning. And for the training service, I've create training about pedagogy, digital learning management project, Digital learning design.
I join my Logo create in this platform. My universe is gamified. I like the life, and I'm very social. I want a card like I'm I. I love Art (painting), Europeen comics. I use in my visual support "permanent maker" font and caracters. I would like cards: elegant, modern, Top class. If you need any information, you can ask me.
thanks for ideas

Target Market(s)

in health industries and training organization for Training manager, instructor, human resources director

Contact Information for Business Card

Phone number : 06 71 38 95 14 , mail: bastiengolmier@quelmoto.fr, web: bastiengolmier.fr , Carrivo

Font styles to use
Sans Serif

Requirements
Must have
• Use my logo and write my 3 services (consulting, training, design)

```html
<!DOCTYPE html>
<html lang="fr">
<head>
<meta charset="utf-8">
<title>Golmier – cartes de visite</title>
<link rel="stylesheet" href="https://fonts.googleapis.com/css2?family=Arimo:wght@400;700&family=Cormorant+SC:wght@500&display=swap">
<style>
  :root {
    --orange: #f37526;
    --grey: #767676;
    --grey-dark: #5b5b5b;
    --ink: #4a4a4a;
    --white: #ffffff;
    --backdrop: #242424;
  }
  * { box-sizing: border-box; margin: 0; padding: 0; }
  html, body { width: 1200px; height: 1015px; overflow: hidden; }
  body {
    background: var(--backdrop);
    font-family: "Arimo", Arial, sans-serif;
    position: relative;
  }
  .card {
    position: absolute;
    left: 300px;
    width: 600px;
    height: 343px;
    overflow: hidden;
  }
  /* Front */
  .card-front { top: 90px; background: var(--orange); }
  .card-front .grey-field {
    position: absolute; inset: 0;
    background: var(--grey);
    clip-path: polygon(0 0, 42% 0, 78% 100%, 0 100%);
  }
  .card-front .brand-mark {
    position: absolute;
    left: 0; right: 0; top: 50%;
    transform: translateY(-50%);
    text-align: center;
    font-weight: 700;
    font-size: 64px;
    letter-spacing: 4px;
    color: var(--white);
  }
  /* Back */
  .card-back { top: 560px; background: var(--white); }
  .brand {
    position: absolute;
    left: 40px; top: 110px;
    width: 230px;
    text-align: center;
  }
  .brand-dot {
    display: block;
    width: 46px; height: 46px;
    margin: 0 auto 10px;
    border-radius: 50%;
    background: var(--orange);
  }
  .brand-name {
    font-weight: 700;
    font-size: 40px;
    letter-spacing: 2px;
    color: var(--orange);
  }
  .divider {
    position: absolute;
    left: 300px; top: 50px;
    width: 1px; height: 150px;
    background: linear-gradient(var(--grey), rgba(118,118,118,0));
  }
  .contact { position: absolute; left: 322px; top: 52px; }
  .person-name {
    font-family: "Cormorant SC", "Times New Roman", serif;
    font-size: 25px;
    color: var(--orange);
    line-height: 1;
  }
  .person-role { font-size: 14px; color: var(--ink); margin-top: 2px; }
  .contact-list { list-style: none; margin-top: 24px; }
  .contact-list li {
    display: flex; align-items: center; gap: 8px;
    font-size: 14px; color: var(--ink); line-height: 20px;
  }
  .contact-list svg { width: 13px; height: 13px; flex: none; }
  .accent { color: var(--orange); }
  .footer-grey {
    position: absolute; left: 0; right: 0; bottom: 0;
    height: 48px; background: var(--grey);
  }
  .footer-orange {
    position: absolute; right: 0; bottom: 0;
    width: 278px; height: 88px;
    background: var(--orange);
    clip-path: polygon(6px 0, 100% 0, 100% 100%, 0 100%);
    border-left: 4px solid var(--white);
  }
  .services {
    position: absolute; right: 0; bottom: 48px;
    width: 278px; height: 40px;
    display: flex; align-items: center; justify-content: center; gap: 6px;
    font-size: 13px; color: var(--white); letter-spacing: .3px;
  }
  .services .sep { width: 7px; height: 7px; border-radius: 50%; background: var(--white); }
  .social {
    position: absolute; left: 150px; bottom: 12px;
    display: flex; align-items: center; gap: 8px;
    font-size: 12px; color: var(--white);
  }
  .social .dot { width: 24px; height: 24px; border-radius: 50%; background: var(--white); }
</style>
</head>
<body>
  <section class="card card-front" aria-label="Recto">
    <div class="grey-field"></div>
    <div class="brand-mark">GOLMIER</div>
  </section>

  <section class="card card-back" aria-label="Verso">
    <div class="brand">
      <span class="brand-dot"></span>
      <div class="brand-name">GOLMIER</div>
    </div>
    <div class="divider"></div>
    <div class="contact">
      <div class="person-name">Julien Morel</div>
      <div class="person-role">Managing Director</div>
      <ul class="contact-list">
        <li>
          <svg viewBox="0 0 16 16"><path fill="#f37526" d="M3.6 1.2l2.3 2.6-1.3 1.8c.9 2 2.4 3.6 4.4 4.6l1.8-1.3 2.6 2.3-1.2 2.2C6.8 13.5 2.5 9.2 1.4 3.4z"/></svg>
          06 71 38 95 14
        </li>
        <li>
          <svg viewBox="0 0 16 16"><rect x="1" y="3" width="14" height="10" fill="#f37526"/><path d="M1 3l7 6 7-6" fill="none" stroke="#fff" stroke-width="1.4"/></svg>
          bastiengolmier@quelmoto.fr
        </li>
        <li>
          <svg viewBox="0 0 16 16"><circle cx="8" cy="8" r="6.5" fill="none" stroke="#f37526" stroke-width="1.4"/><path d="M1.5 8h13M8 1.5c-3 3.5-3 9.5 0 13M8 1.5c3 3.5 3 9.5 0 13" fill="none" stroke="#f37526" stroke-width="1.1"/></svg>
          <span>www.<span class="accent">bastiengolmier</span>.fr</span>
        </li>
      </ul>
    </div>
    <div class="footer-grey"></div>
    <div class="footer-orange"></div>
    <div class="services">
      <span>CONSULTING</span><span class="sep"></span>
      <span>TRAINING</span><span class="sep"></span>
      <span>DESIGN</span>
    </div>
    <div class="social"><span class="dot"></span>Carrivo</div>
  </section>
</body>
</html>
```